Envelope Design - Winner can do follow-up business

- Varnoko.com is a Swiss-based online store selling business shirts and accessories for business men
- Please visit the webpage to make yourself familiar with the company. Although the text is in German, with Plimbo translator you should be able to understand the main content.
- Our clients are mainly business men between 30 and 60 years old. Mostly with a high income working in the service industry (banking, insurance, lawyers, etc.). Sometimes there wives purchase the shirts for them ;-)
- The colors and the logo are given, as they are also used for the print materials (please see files in attachment)
- I am running several businesses and often need a talented web designer --> the winner gets substantial follow-up business
your task:
-for our company we need a new envelope design
-It should be simple and modern
-please use one of the logos in the followings.
-suprise me :)

```html
<!DOCTYPE html>
<html lang="en">
<head>
<meta charset="utf-8">
<title>Varnoko Envelope Set</title>
<link rel="stylesheet" href="https://fonts.googleapis.com/css2?family=Montserrat:wght@500;600&family=Roboto+Slab:wght@400&display=swap">
<style>
  :root {
    --backdrop: #d9d6d2;
    --paper: #ffffff;
    --paper-shade: #ececec;
    --red: #ee3026;
    --red-soft: #f26a4f;
    --black: #000000;
    --gold: #e4d46a;
    --gold-muted: #a59a78;
    --ink: #1b1b1b;
  }
  html, body {
    margin: 0;
    padding: 0;
    width: 1200px;
    height: 953px;
    overflow: hidden;
    background: var(--backdrop);
  }
  .stage {
    position: relative;
    width: 1200px;
    height: 953px;
  }
  .envelope-shapes {
    position: absolute;
    inset: 0;
  }
  .flap-name {
    position: absolute;
    font-family: "Montserrat", sans-serif;
    font-weight: 600;
    font-size: 22px;
    letter-spacing: 0.22em;
    transform: translateX(-50%);
  }
  .flap-name--red { left: 622px; top: 110px; color: var(--red-soft); }
  .flap-name--black { left: 530px; top: 306px; color: var(--gold-muted); }

  .brand {
    position: absolute;
    left: 153px;
    top: 470px;
    display: flex;
    align-items: center;
    gap: 12px;
  }
  .brand-square {
    width: 22px;
    height: 22px;
    background: var(--red);
  }
  .brand-name {
    font-family: "Montserrat", sans-serif;
    font-weight: 500;
    font-size: 34px;
    letter-spacing: 0.06em;
    color: var(--gold);
    line-height: 1;
  }
  .return-address {
    position: absolute;
    left: 160px;
    top: 528px;
    display: flex;
    gap: 14px;
    font-family: "Roboto Slab", serif;
    font-size: 20px;
    line-height: 25px;
    color: var(--ink);
  }
  .return-address svg { margin-top: 2px; }
  .web-address {
    position: absolute;
    left: 162px;
    top: 831px;
    display: flex;
    align-items: center;
    gap: 10px;
    font-family: "Roboto Slab", serif;
    font-size: 20px;
    color: var(--gold);
  }
</style>
</head>
<body>
<main class="stage">
  <svg class="envelope-shapes" width="1200" height="953" viewBox="0 0 1200 953" aria-hidden="true">
    <defs>
      <linearGradient id="backShade" x1="0" y1="0" x2="1" y2="1">
        <stop offset="0" stop-color="#e9e9e9"/>
        <stop offset="1" stop-color="#f8f8f8"/>
      </linearGradient>
    </defs>
    <!-- rear envelope, red flap -->
    <rect class="envelope-rear" x="135" y="50" width="973" height="360" fill="var(--paper)"/>
    <path class="flap-red" d="M135 50 H1108 C1098 95 1090 125 1040 132 L660 196 Q622 206 584 196 L210 132 C160 125 148 95 135 50 Z" fill="var(--red)"/>
    <!-- middle envelope, black flap -->
    <rect class="envelope-middle" x="43" y="240" width="974" height="460" fill="url(#backShade)" stroke="#bdbdbd" stroke-width="1"/>
    <path class="flap-black" d="M43 240 H1017 C1007 285 998 312 950 320 L568 386 Q530 396 492 386 L110 320 C62 312 53 285 43 240 Z" fill="var(--black)"/>
    <!-- front envelope -->
    <rect class="envelope-front" x="136" y="408" width="975" height="460" fill="var(--paper)"/>
    <rect class="front-top-band" x="136" y="408" width="975" height="8" fill="var(--black)"/>
    <rect class="front-red-rule" x="136" y="805" width="975" height="3" fill="var(--red)"/>
    <rect class="front-foot-band" x="136" y="813" width="975" height="55" fill="var(--black)"/>
    <path class="front-corner-tab" d="M972 806 H1076 L1076 812 L1024 850 L972 812 Z" fill="var(--paper)"/>
  </svg>

  <span class="flap-name flap-name--red">VARNOKO</span>
  <span class="flap-name flap-name--black">VARNOKO</span>

  <div class="brand">
    <span class="brand-square"></span>
    <span class="brand-name">VARNOKO</span>
  </div>

  <div class="return-address">
    <svg width="20" height="26" viewBox="0 0 20 26" aria-hidden="true">
      <path d="M10 1 C4.8 1 1 4.8 1 9.6 C1 16 10 25 10 25 C10 25 19 16 19 9.6 C19 4.8 15.2 1 10 1 Z" fill="var(--red)"/>
      <circle cx="10" cy="9.5" r="3.4" fill="var(--paper)"/>
    </svg>
    <p style="margin:0">Street Name, City Name<br>State Zipcode</p>
  </div>

  <div class="web-address">
    <svg width="22" height="22" viewBox="0 0 22 22" aria-hidden="true" fill="none" stroke="var(--red)" stroke-width="1.6">
      <circle cx="11" cy="11" r="9.5"/>
      <ellipse cx="11" cy="11" rx="4.2" ry="9.5"/>
      <line x1="1.5" y1="11" x2="20.5" y2="11"/>
      <line x1="3" y1="6" x2="19" y2="6"/>
      <line x1="3" y1="16" x2="19" y2="16"/>
    </svg>
    <span>www.varnoko.com</span>
  </div>
</main>
</body>
</html>
```